Water ATM Card

Need a design for water ATM cards. Size of card is 3.375 x 2.125 inch
On the Front include the Cedar hollow Logo.
Bottom right corner should have Price $100
On the Back
This card is to be used to access water refills at any Cedar Hollow Water Vending Machines.
Please contact (869) 418 2930 or (869) 534 1276 or email clearflowbox@mailvista.example for any assistance or recharging of card.

```html
<!DOCTYPE html>
<html lang="en">
<head>
<meta charset="UTF-8">
<title>Cedar Hollow Water Card</title>
<link rel="stylesheet" href="https://fonts.googleapis.com/css2?family=Montserrat:wght@400;500;700;800&display=swap">
<style>
  :root {
    --page-bg: #b4b4b4;
    --card-white: #ffffff;
    --brand-blue: #2c4a9c;
    --brand-blue-deep: #27388f;
    --brand-green: #2fa84f;
    --ink: #1f1f2a;
    --back-top: #3d68ad;
    --back-bottom: #2a3d95;
    --back-text: #e6ecfa;
  }
  * { box-sizing: border-box; margin: 0; padding: 0; }
  html, body { width: 1200px; height: 900px; overflow: hidden; }
  body {
    background: var(--page-bg);
    font-family: "Montserrat", sans-serif;
    display: flex;
    flex-direction: column;
    align-items: center;
    justify-content: center;
    gap: 26px;
  }
  .card {
    width: 640px;
    height: 403px;
    position: relative;
    overflow: hidden;
    box-shadow: 0 6px 18px rgba(0,0,0,0.25);
  }

  /* Front */
  .card-front { background: var(--card-white); color: var(--ink); }
  .front-band {
    position: absolute; left: 0; right: 0; bottom: 0; height: 14px;
    background: var(--brand-blue-deep);
  }
  .brand-mark {
    position: absolute; top: 56px; right: 44px;
    display: flex; align-items: center; gap: 10px;
    font-weight: 800; font-size: 30px; letter-spacing: 1px;
    color: var(--brand-blue); text-transform: uppercase;
  }
  .brand-dot { width: 18px; height: 18px; border-radius: 50%; background: var(--brand-green); flex: none; }
  .price {
    position: absolute; top: 158px; right: 44px;
    font-weight: 800; font-size: 34px; color: var(--brand-green);
  }
  .divider {
    position: absolute; top: 214px; left: 34px; right: 40px;
    height: 1.5px; background: var(--brand-blue);
  }
  .holder { position: absolute; top: 146px; left: 36px; }
  .holder-name {
    font-weight: 800; font-size: 21px; color: var(--brand-blue);
    text-transform: uppercase; letter-spacing: 0.5px;
  }
  .holder-role { font-size: 13px; font-weight: 500; margin-top: 4px; text-transform: uppercase; }
  .contact-list {
    position: absolute; top: 232px; left: 36px;
    list-style: none; display: flex; flex-direction: column; gap: 5px;
    font-size: 13.5px; font-weight: 500;
  }
  .contact-list li { display: flex; align-items: center; gap: 9px; }
  .contact-list svg { width: 13px; height: 13px; flex: none; fill: var(--brand-blue); }
  .address {
    position: absolute; top: 236px; right: 44px;
    font-size: 14px; font-weight: 500; line-height: 1.45; text-align: left;
  }

  /* Back */
  .card-back {
    background: linear-gradient(160deg, var(--back-top), var(--back-bottom));
    color: var(--back-text);
  }
  .back-pattern {
    position: absolute; inset: 0;
    background: radial-gradient(ellipse at 70% 30%, rgba(140,170,230,0.35), rgba(40,60,150,0) 70%);
  }
  .back-brand {
    position: absolute; top: 110px; left: 0; right: 0;
    display: flex; justify-content: center; align-items: center; gap: 12px;
    font-weight: 800; font-size: 38px; letter-spacing: 2px;
    text-transform: uppercase; color: #dfe7fb;
  }
  .back-brand .brand-dot { width: 22px; height: 22px; }
  .back-note {
    position: absolute; bottom: 44px; left: 50px; right: 50px; text-align: center;
    font-size: 14px; font-weight: 500; letter-spacing: 0.3px; line-height: 1.6;
  }
</style>
</head>
<body>
  <section class="card card-front" aria-label="Card front">
    <div class="brand-mark"><span class="brand-dot"></span>Cedar Hollow</div>
    <div class="price">Price $100</div>
    <div class="holder">
      <div class="holder-name">Daren Alcott</div>
      <div class="holder-role">Ower</div>
    </div>
    <div class="divider"></div>
    <ul class="contact-list">
      <li><svg viewBox="0 0 24 24"><path d="M6.6 10.8a15 15 0 0 0 6.6 6.6l2.2-2.2a1 1 0 0 1 1-.25 11.4 11.4 0 0 0 3.6.57 1 1 0 0 1 1 1V20a1 1 0 0 1-1 1A17 17 0 0 1 3 4a1 1 0 0 1 1-1h3.5a1 1 0 0 1 1 1c0 1.25.2 2.450.57 3.6a1 1 0 0 1-.25 1z"/></svg>(869) 418 2930</li>
      <li><svg viewBox="0 0 24 24"><path d="M7 1h10a2 2 0 0 1 2 2v18a2 2 0 0 1-2 2H7a2 2 0 0 1-2-2V3a2 2 0 0 1 2-2zm0 3v14h10V4z"/></svg>(869) 534 1276</li>
      <li><svg viewBox="0 0 24 24"><path d="M2 5h20v14H2zm2 2v.5l8 5 8-5V7l-8 5z"/></svg>clearflowbox@mailvista.example</li>
      <li><svg viewBox="0 0 24 24"><path d="M12 2a10 10 0 1 0 0 20 10 10 0 0 0 0-20zm0 2c1.2 0 2.6 2.4 3 6H9c.4-3.6 1.8-6 3-6zm-3 8h6c-.3 3.8-1.8 8-3 8s-2.7-4.2-3-8z"/></svg>www.cedarhollowrefill.example</li>
    </ul>
    <div class="address">450 Birchfield Lane, Ste<br>210 Greyford, TN38120</div>
    <div class="front-band"></div>
  </section>

  <section class="card card-back" aria-label="Card back">
    <div class="back-pattern" role="img" aria-label="Faint repeating brand decoration across the card"></div>
    <div class="back-brand"><span class="brand-dot"></span>Cedar Hollow</div>
    <p class="back-note">This card is to be used to access water refills at any Cedar Hollow Water Vending Machines. Please contact (869) 418 2930 or (869) 534 1276 or email clearflowbox@mailvista.example for any assistance or recharging of card.</p>
  </section>
</body>
</html>
```